Wordpress Theme for Medical Clinics

** Please view updated Sitemap2.pdf doc to clarify some confusion ***

This is a multiuser WordPress subscription site for medical clinics. Please see attachment for sitemap. Please do not include extra content like social media icons, search bars, or images. If you have questions, please ask for clarification.
The site contains the following pages and sub-pages:

1. Home
2. Our Clinic
2a. Our Clinic > Mission
2b. Our Clinic > Services
2c. Our Clinic > Clinic Policies
2d. Our Clinic > Schedules
3. Our Staff
3a. Our Staff > [Staff member page]
4. Resources
4a. Resources > Patient Health (index)
4b. Resources > Patient Health (index) > [post]
4c. Resources > Links
4d. Resources > Forms
5. Alerts
5a. Alerts > [Alert Page]
6. Contact Us

Includes the Following Pages, Subpages, and Content
1. Home
a. About Us
b. Our Staff
c. Bulletins
d. Accepting New Patients (shown as an alert widget)
e. Links
i. Physician Toolbox
ii. Book an Appointment
f. Clinic Policies
i. Show first 3 policies (e.g. Late Arrivals, Missed Appointments, Fees)
ii. Link to Clinic Policies page
g. Primary widget (displayed on all pages)
i. Hours of operation
ii. Contact Info
1. Tel
2. Fax
3. Email
4. Address
5. Get directions (link to Atlas Directions)
2. Our Clinic
a. Main Page
i. Clinic Name
ii. Overview
iii. Languages Spoken
iv. Secondary Navigation
1. Mission
2. Services
3. Clinic Policies
4. Schedules (see attachment)
b. Our Clinic > Mission
c. Our Clinic > Services
i. For each service include service TITLE and DESCRIPTION
d. Our Clinic > Clinic Policies
i. For each policy include policy TITLE and DESCRIPTION
ii. Include the following policies in mockup
1. Late arrivals
2. Missed appointments
3. Fees for missed appointments
4. Referrals and follow-ups
5. Services not covered by RDA
6. Information for LTF patients
7. Medical Legal Reports
e. Our Clinic > Schedules
3. Our Staff
a. Main Page
i. Display a list of staff members. Include NAME and DESIGNATION
b. Our Staff > [Staff Name]
i. Include NAME, PICTURE, DESIGNATION, and BIO
4. Resources
a. Resources > Patient Health
i. Main Page
1. Posts (ordered by date)
a. Title
b. Summary
2. Side Navigation
a. Post Categories
ii. Patient Health > [post title]
1. Title
2. Post Category
3. Date
4. Author
5. Summary
6. Body
b. Resources > Links
1. Secondary Navigation - Categories
a. Sample Categories:
i. Local Services
ii. RDA and Drug Coverage
iii. Mental Health Resources
2. Category page
a. Include the following links in the 'Local Services' category
i. Hypertension clinics
ii. Home Care services
iii. Vaccine Clinics
c. Resources > Forms
i. Display a table with form TITLE and CATEGORY
ii. Side Navigation
1. Form Categories
a. Use the following sample Categories
i. Referrals
ii. Insurance
iii. Intake
iv. Discharge
v. Waivers
5. Alerts
a. Main page
i. List of all Alert posts
1. Include post TITLE as a link to the post
ii. Side Navigation
1. Alerts Archive
a. shown as Month + Number of posts
iii. Alerts > [Alert page]
1. Include TITLE, DATE, AUTHOR, BODY
6. Contact Us
a. Map
b. Hours of operation
c. Address
d. Phone number
e. Fax number
e. Fax number
f. Map
g. Email

Design notes:
- fixed width
- responsive (need designs for mobile, tablet, and desktop)
- simple, dark font, white background
- use Font Awesome icons where needed
- user adds own logo

Target Market(s)

Medical Clinics

Industry/Entity Type

Medical

Number of Pages Required

5+ page

Font styles to use
Serif
Sans Serif

Requirements
Must have
• Please keep designs very simple.
• Examples:
• https://www.quolbin.com/install
• http://www.ventrohax.com/company/about-us
• http://brindlequota.org/
• http://www.trosk.com/
Should not have
• Minimal or no use of shadows and gradients

```html
<!DOCTYPE html>
<html lang="en">
<head>
<meta charset="utf-8">
<title>Clinic Name – Home</title>
<link href="https://fonts.googleapis.com/css2?family=Open+Sans:wght@400;600;700&display=swap" rel="stylesheet">
<style>
:root{
  --blue:#37a0d8;
  --orange:#f7931e;
  --ink:#333;
  --muted:#666;
  --panel:#f2f2f2;
  --rule:#e3e3e3;
  --white:#fff;
}
*{box-sizing:border-box;margin:0;padding:0}
html,body{width:1200px;height:3070px;overflow:hidden;background:var(--white)}
body{font-family:"Open Sans",Arial,sans-serif;color:var(--ink);position:relative}
a{color:inherit;text-decoration:none}

/* Sidebar */
.sidebar{position:absolute;left:0;top:0;width:328px;height:3070px;border-right:2px solid var(--rule);padding:0 0 0 74px}
.brand{margin-top:38px;font-size:30px;font-weight:700;color:var(--orange);white-space:nowrap;line-height:40px}
.nav{margin-top:40px;width:250px;font-size:12.5px;font-weight:700;text-transform:uppercase}
.nav-home{color:var(--orange);height:40px;line-height:26px;border-bottom:1px solid var(--rule)}
.nav-group{padding:14px 0 10px;border-bottom:1px solid var(--rule)}
.nav-group h4{font-size:12.5px;font-weight:600;color:#555;line-height:26px}
.nav-group li{list-style:none;line-height:26px;color:#222}
.nav-group li::before{content:"› ";font-weight:400}
.nav-contact{line-height:40px;padding-top:8px}
.sidebar-foot{position:absolute;left:74px;top:3005px;font-size:12.5px;color:#555;line-height:20px}

/* Main */
.main{position:absolute;left:360px;top:27px;width:813px}
.hero{position:relative;height:413px;background:linear-gradient(180deg,#e9eef2 0%,#d7e4ec 55%,#9fc3dc 100%)}
.hero-arrow{position:absolute;top:180px;width:50px;height:50px;border-radius:50%;background:rgba(60,60,60,.75);display:flex;align-items:center;justify-content:center}
.hero-arrow.prev{left:18px}.hero-arrow.next{right:18px}

.info{display:flex;gap:27px;margin-top:28px;height:346px}
.info-box{flex:1;background:var(--panel)}
.info-head{height:44px;background:var(--blue);color:var(--white);font-size:14px;font-weight:700;text-transform:uppercase;display:flex;align-items:center;padding-left:18px;gap:8px}
.info-body{padding:22px 16px;font-size:13px}
.row{display:flex;line-height:20px;margin-bottom:21px;font-size:12.5px}
.row b{width:88px;flex:none;font-size:11.5px;text-transform:uppercase}
.row em{font-style:normal;color:#999;width:14px;flex:none}
.row span{color:var(--muted)}
.contact .row b{width:76px}
.link{color:var(--blue)}
.btn{display:inline-block;border:3px solid var(--orange);color:var(--orange);font-size:13px;font-weight:700;text-transform:uppercase;padding:9px 16px}

.section{border-top:1px solid var(--rule);position:relative}
.section-title{display:flex;align-items:center;gap:10px;font-size:23px;font-weight:700;text-transform:uppercase;letter-spacing:.5px;height:56px}
.about{margin-top:40px;padding-top:10px}
.about-wrap{display:flex;justify-content:space-between}
.about p{width:445px;font-size:16px;line-height:30px;color:#555}
.about-photo{width:348px;height:228px;margin-top:8px;background:linear-gradient(135deg,#c9d3d8,#8fa1ab 60%,#dfe6ea)}

.staff{margin-top:36px;padding-top:8px}
.staff-row{display:flex;height:86px;margin-bottom:8px;background:var(--panel)}
.staff-tag{position:relative;width:187px;background:var(--blue);color:var(--white);padding:10px 14px;font-size:12.5px}
.staff-tag b{display:block;font-size:12px;text-transform:uppercase}
.staff-tag::after{content:"";position:absolute;right:-10px;top:12px;border:8px solid transparent;border-left:10px solid var(--blue);border-right:0}
.staff-text{flex:1;padding:8px 16px 0 22px;font-size:13.5px;line-height:23px;color:#555}
.staff-text i{font-size:12.5px}
.staff .btn{margin-top:52px}

.alerts{margin-top:30px;padding-top:10px}
.alerts-wrap{display:flex;justify-content:space-between;height:374px;margin-top:4px}
.calendar{width:533px;background:var(--panel);position:relative;padding:28px 32px 0}
.cal-top{display:flex;justify-content:space-between;font-size:13px;color:#555;padding:0 18px}
.cal-grid{width:100%;border-collapse:collapse;margin-top:20px;font-size:13px;color:#555;text-align:center}
.cal-grid th{font-weight:600;height:36px}
.cal-grid td{height:42px}
.cal-grid .today span{display:inline-block;width:28px;height:28px;line-height:28px;border-radius:50%;background:var(--orange);color:var(--white)}
.cal-grid .mark{text-decoration:underline}
.cal-prev{position:absolute;left:12px;top:200px;width:12px;height:12px;border:3px solid #333;border-radius:50%}
.cal-next{position:absolute;right:12px;top:198px}
.alert-card{width:264px;background:var(--orange);color:var(--white);padding:14px 16px;font-size:12.5px;line-height:20px}
.alert-card h3{font-size:13px;font-weight:700;text-transform:uppercase;line-height:19px}
.alert-card time{display:block;font-size:11.5px;margin:4px 0 14px}

.policies{margin-top:62px;padding-top:8px}
.policies ul{list-style:none;font-size:14px;text-transform:uppercase;color:#444;line-height:26px;margin-top:2px}
.policies li::before{content:"→ ";color:#999}
.policies .btn{margin-top:30px}

.location{margin-top:56px;padding-top:8px}
.map{margin-top:8px;height:427px;background:linear-gradient(135deg,#e8e2c8,#d9d3b6 40%,#c9d6df 100%)}
</style>
</head>
<body>

<aside class="sidebar">
  <div class="brand">CLINIC NAME</div>
  <nav class="nav">
    <div class="nav-home">Home</div>
    <div class="nav-group">
      <h4>Our Clinic</h4>
      <ul><li>Mission</li><li>Services</li><li>Clinic Policies</li><li>Schedules</li></ul>
    </div>
    <div class="nav-group">
      <h4>Our Staff</h4>
      <ul><li>Staff Member Page</li></ul>
    </div>
    <div class="nav-group">
      <h4>Resources</h4>
      <ul><li>Patient Health</li><li>Patient Health</li><li>Post</li><li>Links</li><li>Forms</li></ul>
    </div>
    <div class="nav-group">
      <h4>Alerts</h4>
      <ul><li>Alert</li></ul>
    </div>
    <div class="nav-contact">Contact Us</div>
  </nav>
  <div class="sidebar-foot">©2015 Clinic Name. All Rights Reserved<br>Terms &amp; Privacy Policy | Sitemap</div>
</aside>

<main class="main">
  <div class="hero" role="img" aria-label="Photo of three smiling clinic staff members in white coats">
    <div class="hero-arrow prev"><svg width="18" height="18" viewBox="0 0 18 18"><path d="M12 2 5 9l7 7" fill="none" stroke="#fff" stroke-width="3"/></svg></div>
    <div class="hero-arrow next"><svg width="18" height="18" viewBox="0 0 18 18"><path d="M6 2l7 7-7 7" fill="none" stroke="#fff" stroke-width="3"/></svg></div>
  </div>

  <div class="info">
    <div class="info-box">
      <div class="info-head"><svg width="16" height="16" viewBox="0 0 16 16"><circle cx="6" cy="4.5" r="3.2" fill="#fff"/><path d="M0 15c0-4 2.5-6 6-6s6 2 6 6z" fill="#fff"/><path d="M13 4v6M10 7h6" stroke="#fff" stroke-width="2"/></svg>New Patients</div>
      <div class="info-body">
        <p style="color:var(--muted);margin-bottom:14px">Accepting new patients</p>
        <a class="btn" href="#">Contact Us</a>
      </div>
    </div>
    <div class="info-box">
      <div class="info-head"><svg width="15" height="15" viewBox="0 0 16 16"><circle cx="8" cy="8" r="6.5" fill="none" stroke="#fff" stroke-width="2"/><path d="M8 4v4.5h3" fill="none" stroke="#fff" stroke-width="2"/></svg>Hours of Operation</div>
      <div class="info-body">
        <div class="row"><b>Monday</b><em>:</em><span>8:00am - 6:00pm</span></div>
        <div class="row"><b>Tuesday</b><em>:</em><span>8:00am - 6:00pm</span></div>
        <div class="row"><b>Wednesday</b><em>:</em><span>8:00am - 6:00pm</span></div>
        <div class="row"><b>Thursday</b><em>:</em><span>8:00am - 6:00pm</span></div>
        <div class="row"><b>Friday</b><em>:</em><span>8:00am - 6:00pm</span></div>
        <div class="row"><b>Saturday</b><em>:</em><span>9:00am - 4:00pm</span></div>
        <div class="row"><b>Sunday</b><em>:</em><span>9:00am - 4:00pm</span></div>
      </div>
    </div>
    <div class="info-box contact">
      <div class="info-head"><svg width="16" height="12" viewBox="0 0 16 12"><rect x="0" y="0" width="16" height="12" rx="1" fill="#fff"/><path d="M1 1l7 6 7-6" fill="none" stroke="#37a0d8" stroke-width="1.6"/></svg>Contact Info</div>
      <div class="info-body">
        <div class="row"><b>Telephone</b><em>:</em><span>555 010 4477</span></div>
        <div class="row"><b>Fax</b><em>:</em><span>555 010 4477</span></div>
        <div class="row"><b>Email</b><em>:</em><span class="link">contact@clinicmail.co</span></div>
        <div class="row"><b>Address</b><em>:</em><span>48 Larkspur Road,<br>Harrowfield, B.C.<br>Canada, K4R2T9</span></div>
        <div class="row"><b>Directions</b><em>:</em><span class="link">Atlas Directions</span></div>
      </div>
    </div>
  </div>

  <section class="section about">
    <h2 class="section-title"><svg width="20" height="22" viewBox="0 0 20 22"><rect x="2" y="3" width="16" height="18" fill="none" stroke="#333" stroke-width="2"/><rect x="6" y="0" width="8" height="5" fill="#333"/><path d="M10 8v8M6 12h8" stroke="#333" stroke-width="2.4"/></svg>About Our Clinic</h2>
    <div class="about-wrap">
      <p>Lorem Ipsum is simply dummy text of the printing and typesetting industry. Lorem Ipsum has been the industry's standard dummy text ever since the 1500s, when an unknown printer took a galley of type and scrambled it to make a type specimen book. It has survived not only five centuries, but also the leap into electronic typesetting desktop publishing software like Folio PageSet including versions of Lorem Ipsum.</p>
      <div class="about-photo" role="img" aria-label="Photo of a bright clinic corridor"></div>
    </div>
  </section>

  <section class="section staff">
    <h2 class="section-title"><svg width="26" height="20" viewBox="0 0 26 20"><circle cx="13" cy="5" r="4" fill="#333"/><circle cx="5" cy="7" r="3" fill="#333"/><circle cx="21" cy="7" r="3" fill="#333"/><path d="M6 19c0-5 3-8 7-8s7 3 7 8zM0 17c0-4 2-6 5-6l1 1c-1 1-2 3-2 5zM26 17c0-4-2-6-5-6l-1 1c1 1 2 3 2 5z" fill="#333"/></svg>Our Staff</h2>
    <div class="staff-row"><div class="staff-tag"><b>Dr. John Smith, MD</b>Physician</div><div class="staff-text">In publishing and graphic design, lorem ipsum is a filler text commonly used to demonstrate the graphic elements of a document or visual presentation.<br><i>(Read more)</i></div></div>
    <div class="staff-row"><div class="staff-tag"><b>Dr. Jane Doe, MD</b>Therapist</div><div class="staff-text">In publishing and graphic design, lorem ipsum is a filler text commonly used to demonstrate the graphic elements of a document or visual presentation.<br><i>(Read more)</i></div></div>
    <div class="staff-row"><div class="staff-tag"><b>Dr. Willson, MD</b>Radiologist</div><div class="staff-text">In publishing and graphic design, lorem ipsum is a filler text commonly used to demonstrate the graphic elements of a document or visual presentation.<br><i>(Read more)</i></div></div>
    <div class="staff-row"><div class="staff-tag"><b>Dr. John Smith, MD</b>Physician</div><div class="staff-text">In publishing and graphic design, lorem ipsum is a filler text commonly used to demonstrate the graphic elements of a document or visual presentation.<br><i>(Read more)</i></div></div>
    <div class="staff-row"><div class="staff-tag"><b>Dr. John Smith, MD</b>Physician</div><div class="staff-text">In publishing and graphic design, lorem ipsum is a filler text commonly used to demonstrate the graphic elements of a document or visual presentation.<br><i>(Read more)</i></div></div>
    <a class="btn" href="#">View All Staff</a>
  </section>

  <section class="section alerts">
    <h2 class="section-title"><svg width="20" height="22" viewBox="0 0 20 22"><path d="M10 1c-4 0-6 3-6 7v5l-3 4h18l-3-4V8c0-4-2-7-6-7z" fill="#333"/><circle cx="10" cy="19.5" r="2.5" fill="#333"/></svg>Alerts</h2>
    <div class="alerts-wrap">
      <div class="calendar">
        <div class="cal-top"><span>2013</span><span>MARCH, 2015</span><span>2016</span></div>
        <table class="cal-grid">
          <tr><th>SUN</th><th>MON</th><th>TUE</th><th>WED</th><th>THUR</th><th>FRI</th><th>SAT</th></tr>
          <tr><td>1</td><td>2</td><td>3</td><td>4</td><td>5</td><td>6</td><td>7</td></tr>
          <tr><td>8</td><td class="today"><span>9</span></td><td>10</td><td>11</td><td>12</td><td>13</td><td>14</td></tr>
          <tr><td>15</td><td>16</td><td class="mark">17</td><td>18</td><td class="mark">19</td><td>20</td><td>21</td></tr>
          <tr><td>22</td><td>23</td><td>24</td><td>25</td><td>26</td><td>27</td><td class="mark">28</td></tr>
          <tr><td>29</td><td>30</td><td>31</td><td></td><td></td><td></td><td></td></tr>
        </table>
        <span class="cal-prev"></span>
        <svg class="cal-next" width="16" height="16" viewBox="0 0 16 16"><circle cx="8" cy="8" r="8" fill="#f7931e"/><path d="M6 4l4 4-4 4" fill="none" stroke="#fff" stroke-width="2"/></svg>
      </div>
      <article class="alert-card">
        <h3>A Handy Lorem Ipsum is make dummy text for layout needs</h3>
        <time>9 March 2015</time>
        <p>In publishing and graphic design, lorem ipsum is a filler text commonly used to demonstrate the graphic elements of a document or visual pre sentation. Lorem ipsum dolor sit amet, consectetuer adipiscing elit, sed diam nonummy nibh euismod tincidunt ut laoreet dolore magna aliquam erat volutpat. Ut wisi enim ...</p>
      </article>
    </div>
  </section>

  <section class="section policies">
    <h2 class="section-title"><svg width="18" height="22" viewBox="0 0 18 22"><path d="M0 0h12l6 6v16H0z" fill="#333"/><path d="M12 0v6h6" fill="#999"/></svg>Clinic Policies</h2>
    <ul><li>Late Arrivals</li><li>Missed Appointments</li><li>Fees</li></ul>
    <a class="btn" href="#">View All Clinic Policies</a>
  </section>

  <section class="section location">
    <h2 class="section-title"><svg width="16" height="22" viewBox="0 0 16 22"><path d="M8 0C3.6 0 0 3.4 0 7.8 0 13 8 22 8 22s8-9 8-14.2C16 3.4 12.4 0 8 0z" fill="#333"/><circle cx="8" cy="8" r="3" fill="#fff"/></svg>Our Location</h2>
    <div class="map" role="img" aria-label="Street map showing the clinic location in the city centre"></div>
  </section>
</main>

</body>
</html>
```